Corvana Tongue Works, LLC

We need a business card that includes information about our business and conveys a reliable business that provides document translation services and interpreters for a variety of corporate and individual clients. We want to come across as professional, reliable, yet approachable. It should include the following on one side:

ESL / ENL Language Classes, Private Lessons, and Online Tutors
PLEXA Training and Testing
Translating & Interpreting Services
Contact us about Over-the-Phone Interpreting in over 200 languages
24/7/365
www.corvanatongue.example

The other side should include (555) 481-3062

Rhoda Pelling, President
482 Garnet Ave., Ste. 219
Indianapolis, IN 40917

Please add USA as part of the address. Also, please add rmpelling@corvanatongueworks.example as the e-mail address. Thank you.

Target Market(s)

Business professionals, their families, the international community

Industry/Entity Type

Business

Contact Information for Business Card

24/7/365
www.corvanatongue.example

(555) 481-3062

Rhoda Pelling, President
482 Garnet Ave., Ste. 219
Indianapolis, IN 40917
USA

Font styles to use
Sans Serif

Colors

Designer to choose colors to be used in the design.

Requirements
Must have
• See project description
• e-mail address and web address
• Phone number
Nice to have
• a globe
• physical address
Should not have
• Should not have the same color scheme as other agencies in our market in Indiana unless it is blue and black. No purple or yellow.

```html
<!DOCTYPE html>
<html lang="en">
<head>
<meta charset="utf-8">
<title>Corvana Tongue Works — Business Card</title>
<link href="https://fonts.googleapis.com/css2?family=Roboto:wght@300;400;500;700&display=swap" rel="stylesheet">
<style>
  :root{
    --stage:#2b2b2d;
    --card:#0b0b0c;
    --card-edge:#1c1c1e;
    --ink:#ffffff;
    --ink-soft:#d9d9d9;
    --accent:#3fa3dd;
  }
  *{box-sizing:border-box;margin:0;padding:0}
  html,body{width:1200px;height:896px;overflow:hidden}
  body{
    background:var(--stage);
    font-family:"Roboto",Arial,sans-serif;
    color:var(--ink);
    display:flex;align-items:center;justify-content:center;gap:40px;
  }
  .card{
    width:540px;height:309px;border-radius:22px;
    background:linear-gradient(160deg,#1a1a1c 0%,var(--card) 55%);
    border:1px solid var(--card-edge);
    box-shadow:0 18px 40px rgba(0,0,0,.55);
    position:relative;overflow:hidden;
  }

  /* Front */
  .front{padding:26px 32px;text-align:center}
  .brand{display:flex;align-items:center;justify-content:center;gap:14px;margin-bottom:20px}
  .brand-dot{width:46px;height:46px;border-radius:50%;background:var(--accent);flex:none}
  .brand-name{font-size:27px;font-weight:400;line-height:1.1;color:var(--ink);text-align:left}
  .services{list-style:none;font-size:14.5px;font-weight:500;line-height:1.45;color:var(--ink)}
  .rule{height:2px;background:var(--accent);margin:14px 0 12px}
  .callout{font-size:14.5px;font-weight:500;line-height:1.45}
  .front-web{margin-top:6px;font-size:14.5px;font-weight:500;line-height:1.45}

  /* Back */
  .back{display:flex;align-items:center;padding-right:16px}
  .back-mark{width:190px;flex:none;display:flex;flex-direction:column;align-items:center;justify-content:center;gap:12px;padding-left:14px}
  .back-mark .disc{width:140px;height:140px;border-radius:50%;background:var(--accent)}
  .back-mark .name{font-size:20px;font-weight:400;color:var(--ink)}
  .divider{width:2px;height:150px;background:var(--accent);margin:0 22px 0 8px;flex:none}
  .details{font-size:14px;font-weight:400;line-height:1.5;color:var(--ink);min-width:0}
  .person{font-size:25px;font-weight:500;color:var(--accent);text-transform:uppercase;letter-spacing:.5px;line-height:1.1}
  .role{font-size:14px;margin-bottom:10px}
  .address{margin-bottom:10px}
  .contact{list-style:none}
  .contact li{display:flex;align-items:center;gap:8px;white-space:nowrap}
  .contact svg{width:12px;height:12px;flex:none}
  .web-domain{color:var(--accent)}
</style>
</head>
<body>

<section class="card front">
  <div class="brand">
    <span class="brand-dot"></span>
    <span class="brand-name">Corvana Tongue Works, LLC</span>
  </div>
  <ul class="services">
    <li>ESL / ENL Language Classes, Private Lessons, and Online Tutors</li>
    <li>PLEXA Training and Testing</li>
    <li>Translating &amp; Interpreting Services</li>
  </ul>
  <div class="rule"></div>
  <p class="callout">Contact us about Over-the-Phone Interpreting in over 200 languages<br>24/7/365</p>
  <p class="front-web">www.<span class="web-domain">corvanatongue</span>.example</p>
</section>

<section class="card back">
  <div class="back-mark">
    <span class="disc"></span>
    <span class="name">Corvana</span>
  </div>
  <div class="divider"></div>
  <div class="details">
    <p class="person">Rhoda Pelling</p>
    <p class="role">President</p>
    <p class="address">482 Garnet Ave., Ste. 219<br>Indianapolis, IN 40917 USA</p>
    <ul class="contact">
      <li>
        <svg viewBox="0 0 12 12" fill="var(--ink)"><path d="M2.5 1h2l1 2.6-1.3 1a6 6 0 0 0 2.9 2.9l1-1.3L10.7 7v2c0 .6-.5 1-1 1A8.8 8.8 0 0 1 1.5 2c0-.5.4-1 1-1z"/></svg>
        (555) 481-3062
      </li>
      <li>
        <svg viewBox="0 0 12 12" fill="none" stroke="var(--ink)" stroke-width="1.2"><rect x="1" y="2.5" width="10" height="7"/><path d="M1 2.5l5 4 5-4"/></svg>
        rmpelling@corvanatongueworks.example
      </li>
      <li>
        <svg viewBox="0 0 12 12" fill="none" stroke="var(--ink)" stroke-width="1.1"><circle cx="6" cy="6" r="5"/><ellipse cx="6" cy="6" rx="2.2" ry="5"/><path d="M1 6h10"/></svg>
        <span>www.<span class="web-domain">corvanatongue</span>.example</span>
      </li>
    </ul>
  </div>
</section>

</body>
</html>
```